New Business Card for Software Company

We are looking at rebranding a 10 year old company that specializes in PDF and DWF solutions for Architects and Engineers. We will attach the new company logo that we are going with so you can work with that and complimentary colors.
The sample information we would like on the business card is:
Gerald Pinfold
Vice President
4738 W. Harrowgate Lane. STE 305
PMB#417
Mesa, AZ 85374
866-392-5074 US Toll Free
123-456-3190 Cell
gpinfold@plavorix.com
The old tag line that we had on the business cars was.
Delivering Dependable Drawing File Tools and Publishing Services to Design Firms Worldwide.
If you have an idea for a better tag line we are open to that also.
Updates
We would like to thank all of the Designers for their wonderful work. We apologize that we will not have the time to provide feedback to everyone. There is just so many innovative and professional designs that you have all created making our decision even harder.
Target Market(s)
Architects and Engineers
Industry/Entity Type
Business
Look and feel

```html
<!DOCTYPE html>
<html lang="en">
<head>
<meta charset="utf-8">
<title>Plavorix Business Card</title>
<link rel="stylesheet" href="https://fonts.googleapis.com/css2?family=Source+Sans+3:wght@400;600;700&display=swap">
<style>
  :root {
    --stage: #e9e6e2;
    --card-white: #ffffff;
    --brand-orange: #ee6a1f;
    --band-red: #c9251f;
    --band-orange: #f47b20;
    --band-amber: #f7a23a;
    --ink-grey: #555555;
    --back-grey: #666666;
    --text-light: #ffffff;
    --tagline: #e6e6e6;
  }
  * { box-sizing: border-box; margin: 0; padding: 0; }
  html, body {
    width: 1200px; height: 720px; overflow: hidden;
    background: var(--stage);
    font-family: "Source Sans 3", "Myriad Pro", Arial, sans-serif;
  }
  .stage {
    width: 1200px; height: 720px;
    display: flex; align-items: center; justify-content: center; gap: 40px;
  }
  .card {
    width: 540px; height: 309px; position: relative; overflow: hidden;
    box-shadow: 0 6px 18px rgba(0,0,0,.18);
  }

  /* Front */
  .card-front { background: var(--card-white); }
  .front-brand {
    position: absolute; left: 40px; top: 58px;
    display: flex; align-items: center; gap: 14px;
  }
  .brand-dot {
    width: 50px; height: 50px; border-radius: 50%;
    background: var(--brand-orange);
  }
  .brand-name {
    font-weight: 700; font-size: 58px; line-height: 1;
    color: var(--brand-orange); letter-spacing: -1px;
  }
  .holder {
    position: absolute; left: 132px; top: 128px;
    font-size: 17px; color: var(--ink-grey);
  }
  .holder-name { font-weight: 700; color: var(--brand-orange); }
  .contact-band {
    position: absolute; left: 0; right: 0; bottom: 0; height: 142px;
    background: linear-gradient(180deg, var(--band-red) 0%, var(--band-orange) 55%, var(--band-amber) 100%);
    border-top: 2px solid #b7b7b7;
  }
  .address {
    position: absolute; right: 290px; top: 30px;
    text-align: right; color: var(--text-light);
    font-style: normal; font-size: 14px; line-height: 1.6;
    white-space: nowrap;
  }
  .divider {
    position: absolute; left: 262px; top: 30px; width: 1px; height: 76px;
    background: rgba(255,255,255,.7);
  }
  .contacts {
    position: absolute; left: 276px; top: 30px;
    list-style: none; color: var(--text-light);
    font-size: 14px; line-height: 1.6;
    white-space: nowrap;
  }
  .contacts li { display: flex; align-items: center; gap: 7px; }
  .contacts svg { width: 12px; height: 12px; fill: var(--text-light); flex: none; }

  /* Back */
  .card-back { background: var(--back-grey); }
  .back-brand {
    position: absolute; left: 0; right: 0; top: 70px;
    display: flex; align-items: center; justify-content: center; gap: 14px;
  }
  .back-brand .brand-dot { width: 56px; height: 56px; }
  .back-brand .brand-name { font-size: 60px; }
  .tagline {
    position: absolute; left: 0; right: 0; bottom: 48px;
    text-align: center; color: var(--tagline);
    font-size: 18px; line-height: 1.35;
  }
</style>
</head>
<body>
<main class="stage">
  <section class="card card-front" aria-label="Business card front">
    <div class="front-brand">
      <span class="brand-dot"></span>
      <span class="brand-name">Plavorix</span>
    </div>
    <p class="holder"><span class="holder-name">Gerald Pinfold,</span> Vice President</p>
    <div class="contact-band">
      <address class="address">
        4738 W. Harrowgate Lane. STE 305<br>
        PMB#417, Mesa<br>
        AZ 85374
      </address>
      <span class="divider"></span>
      <ul class="contacts">
        <li>
          <svg viewBox="0 0 24 24" aria-hidden="true"><path d="M6.6 10.8a15.1 15.1 0 0 0 6.6 6.6l2.2-2.2a1 1 0 0 1 1-.25 11.4 11.4 0 0 0 3.6.57 1 1 0 0 1 1 1V20a1 1 0 0 1-1 1A17 17 0 0 1 3 4a1 1 0 0 1 1-1h3.5a1 1 0 0 1 1 1c0 1.25.2 2.45.57 3.57a1 1 0 0 1-.25 1z"/></svg>
          866-392-5074 US(TF)
        </li>
        <li>
          <svg viewBox="0 0 24 24" aria-hidden="true"><path d="M7 1h10a2 2 0 0 1 2 2v18a2 2 0 0 1-2 2H7a2 2 0 0 1-2-2V3a2 2 0 0 1 2-2zm0 3v14h10V4zm5 15.5a1 1 0 1 0 0 2 1 1 0 0 0 0-2z"/></svg>
          123-456-3190
        </li>
        <li>
          <svg viewBox="0 0 24 24" aria-hidden="true"><path d="M2 5h20v14H2zm2 2v.5l8 5 8-5V7zm0 2.8V17h16V9.8l-8 5z"/></svg>
          gpinfold@plavorix.com
        </li>
      </ul>
    </div>
  </section>

  <section class="card card-back" aria-label="Business card back">
    <div class="back-brand">
      <span class="brand-dot"></span>
      <span class="brand-name">Plavorix</span>
    </div>
    <p class="tagline">Delivering Dependable Drawing File Tools and<br>Publishing Services to Design Firms Worldwide</p>
  </section>
</main>
</body>
</html>
```